Business Card Design

We like to use greens as you will see in our logo (but not TOO much green). We are a Dental Clinic in a somewhat eccentric community. We do not like the dated sharp designs which we see many dentists use. We're looking for something bright and fresh while still maintaining the integrity of the profession. Elegance is not necessarily what we are going for... we need for the design to be "mature" but also up-lifting.

See our logo.
Updates

Project Deadline Extended
Reason: We have 5 designs which we like. But we'd like to see a few more before committing to a design.

Project Deadline Extended
Reason: We are awaiting revisions to this project. We are still welcoming designs while we wait to see if designers are able to provide to us the revisions we require in order to proceed with a selection.

Target Market(s)

Younger families - ages late 20's to early 40's

Industry/Entity Type

Business

Contact Information for Business Card

Corwel T. Banfry DDS 2730 W. Halvert Rd. Ste. 7 Larkfield, OH 48391 (248)555-0174 FX (248)555-0189 info@BrightwellDentalCareMi.com BrigthwellDentalCareMi.com on the back of the card we need an appointment reminder (For____ Date___ Time____) with "If you are unable to keep your appointment, kindly give 48 hours notice" at the bottom. No use of teeth in the design. DOUBLE SIDED DESIGN

Requirements
Should not have
• The use of pictures of teeth

```html
<!DOCTYPE html>
<html lang="en">
<head>
<meta charset="utf-8">
<title>Brightwell Dental Care – Business Card</title>
<link rel="stylesheet" href="https://fonts.googleapis.com/css2?family=Source+Sans+3:ital,wght@0,400;0,600;0,700;1,400&family=Cinzel:wght@500&display=swap">
<style>
  :root {
    --forest: #1d6b32;
    --leaf: #7cc242;
    --ink: #2b2b2b;
    --paper: #ffffff;
    --backdrop: #e9e6e0;
    --rule: #555555;
    --edge: #3a3a3a;
  }
  * { box-sizing: border-box; margin: 0; padding: 0; }
  html, body { width: 1200px; height: 1178px; overflow: hidden; }
  body {
    background: var(--backdrop);
    font-family: "Source Sans 3", Arial, sans-serif;
    color: var(--ink);
    position: relative;
  }
  .card {
    position: absolute;
    width: 915px;
    height: 522px;
    background: var(--paper);
    border-radius: 40px;
    overflow: hidden;
  }
  .card--front { left: 43px; top: 47px; }
  .card--back { left: 267px; top: 621px; border: 2px solid var(--edge); }

  /* brand wordmark */
  .brand {
    position: absolute;
    display: flex;
    align-items: center;
    gap: 14px;
    color: var(--forest);
    font-weight: 600;
    line-height: 1.02;
  }
  .brand__dot { border-radius: 50%; background: var(--leaf); flex: none; }
  .card--front .brand { left: 0; right: 0; top: 82px; justify-content: center; font-size: 58px; }
  .card--front .brand__dot { width: 42px; height: 42px; }
  .card--back .brand { left: 73px; top: 30px; font-size: 34px; }
  .card--back .brand__dot { width: 26px; height: 26px; }

  .doctor {
    position: absolute; left: 0; right: 0; top: 282px;
    text-align: center; color: var(--forest);
    font-size: 29px; font-weight: 700;
  }
  .doctor span { font-weight: 400; font-size: 25px; color: var(--ink); }

  .band { position: absolute; left: 0; top: 0; width: 915px; height: 522px; }

  .contact {
    position: absolute; left: 0; right: 0;
    display: flex; justify-content: center; align-items: center; gap: 18px;
    color: var(--paper); font-size: 22px; line-height: 1;
  }
  .contact__item { display: inline-flex; align-items: center; gap: 6px; }
  .contact__item svg { width: 18px; height: 18px; fill: var(--paper); }
  .contact--phones { top: 381px; }
  .contact--web { top: 421px; }
  .contact--address { top: 473px; }

  /* appointment side */
  .appt-title {
    position: absolute; left: 76px; top: 170px;
    font-family: "Cinzel", Georgia, serif;
    font-size: 34px; color: var(--forest); letter-spacing: 0.5px;
  }
  .field { position: absolute; font-size: 25px; color: #333; line-height: 1; }
  .dots { position: absolute; border-bottom: 2px dotted var(--rule); height: 0; }
  .slot {
    position: absolute; height: 36px;
    border: 2px solid var(--edge); border-radius: 4px;
  }
  .day {
    position: absolute; right: 97px;
    font-size: 25px; font-weight: 600; color: #222;
    transform: translateY(-50%);
  }
  .day-box {
    position: absolute; left: 834px; width: 56px; height: 32px;
    border: 2px solid var(--edge); border-radius: 3px;
    transform: translateY(-50%);
  }
  .notice {
    position: absolute; left: 75px; top: 452px;
    font-size: 25px; font-style: italic; color: #222;
  }
</style>
</head>
<body>

<section class="card card--front" aria-label="Business card front">
  <div class="brand"><span class="brand__dot"></span><span>Brightwell<br>Dental Care</span></div>
  <p class="doctor">Corwel T. Banfry, <span>DDS</span></p>

  <svg class="band" viewBox="0 0 915 522" aria-hidden="true">
    <path d="M0 426 Q457 254 915 426" fill="none" stroke="var(--leaf)" stroke-width="6"/>
    <path d="M0 441 Q457 283 915 441 L915 522 L0 522 Z" fill="var(--forest)"/>
  </svg>

  <div class="contact contact--phones">
    <span class="contact__item">
      <svg viewBox="0 0 20 20"><path d="M5 2l3 4-2 2c1 2 3 4 5 5l2-2 4 3-2 3C9 17 3 11 2 4z"/></svg>
      (555)555-0174
    </span>
    <span class="contact__item">
      <svg viewBox="0 0 20 20"><path d="M4 8l2-4h8l2 4h2v6h-2v2h-3v-2H7v2H4v-2H2V8z"/></svg>
      (555)555-0189
    </span>
  </div>
  <div class="contact contact--web">
    <span class="contact__item">
      <svg viewBox="0 0 20 20"><path d="M2 5h16v11H2z M3 6l7 5 7-5" stroke="var(--forest)" stroke-width="1.4"/></svg>
      info@BrightwellDentalCareMi.com
    </span>
    <span class="contact__item">
      <svg viewBox="0 0 20 20"><circle cx="10" cy="10" r="8"/><path d="M2 10h16M10 2c-4 4-4 12 0 16M10 2c4 4 4 12 0 16" stroke="var(--forest)" stroke-width="1.3" fill="none"/></svg>
      BrigthwellDentalCareMi.com
    </span>
  </div>
  <div class="contact contact--address">2730 W. Halvert Rd. Ste. 7 Larkfield, OH 48391</div>
</section>

<section class="card card--back" aria-label="Appointment card back">
  <div class="brand"><span class="brand__dot"></span><span>Brightwell<br>Dental Care</span></div>
  <h2 class="appt-title">YOUR APPOINTMENT</h2>

  <span class="field" style="left:78px; top:248px;">Name :</span>
  <span class="dots" style="left:182px; width:505px; top:266px;"></span>

  <span class="field" style="left:78px; top:314px;">Date :</span>
  <span class="dots" style="left:182px; width:166px; top:332px;"></span>
  <span class="field" style="left:357px; top:314px;">Time :</span>
  <span class="dots" style="left:440px; width:158px; top:332px;"></span>
  <span class="field" style="left:602px; top:314px;">am / pm</span>

  <span class="field" style="left:78px; top:380px;">Next Appointment</span>
  <span class="slot" style="left:326px; width:164px; top:373px;"></span>
  <span class="slot" style="left:528px; width:164px; top:373px;"></span>

  <span class="day" style="top:92px;">MON</span><span class="day-box" style="top:92px;"></span>
  <span class="day" style="top:155px;">TUE</span><span class="day-box" style="top:155px;"></span>
  <span class="day" style="top:218px;">WED</span><span class="day-box" style="top:218px;"></span>
  <span class="day" style="top:284px;">THU</span><span class="day-box" style="top:284px;"></span>
  <span class="day" style="top:341px;">FRI</span><span class="day-box" style="top:341px;"></span>
  <span class="day" style="top:397px;">SAT</span><span class="day-box" style="top:397px;"></span>

  <p class="notice">If you are unable to keep your appointment, kindly give 48 hours notice</p>
</section>

</body>
</html>
```